PWNF Traditional Business Card Project

Please see attached....just a simple business card... on attachment- please use the exact font, style, etc as the attached "Ned Farley Broughton" card... however, replace with the "Walter Augustin Pryde" text and address below the card.

```html
<!DOCTYPE html>
<html lang="en">
<head>
<meta charset="utf-8">
<title>PWNF Business Card – Walter Augustin Pryde</title>
<link rel="stylesheet" href="https://fonts.googleapis.com/css2?family=Tinos:wght@700&family=Montserrat:wght@500;600&display=swap">
<style>
  :root {
    --page-bg: #efefef;
    --card-bg: #e5e4e1;
    --ink: #2a2a2a;
    --card-shadow: rgba(0, 0, 0, 0.25);
  }
  html, body {
    margin: 0;
    padding: 0;
    width: 1200px;
    height: 1028px;
    overflow: hidden;
    background: var(--page-bg);
  }
  .card {
    position: absolute;
    left: 75px;
    top: 214px;
    width: 1050px;
    height: 600px;
    background: var(--card-bg);
    box-shadow: 0 3px 8px var(--card-shadow);
    color: var(--ink);
  }
  .serif-caps {
    font-family: "Tinos", "Times New Roman", serif;
    font-weight: 700;
    font-variant: small-caps;
    letter-spacing: 0.5px;
    line-height: 1;
    margin: 0;
  }
  .wide-sans {
    font-family: "Montserrat", Arial, sans-serif;
    font-weight: 600;
    text-transform: uppercase;
    letter-spacing: 1.5px;
    line-height: 1;
    margin: 0;
  }
  .firm {
    position: absolute;
    left: 62px;
    top: 52px;
  }
  .firm-name {
    font-size: 64px;
  }
  .firm-suffix {
    font-size: 21px;
    margin-top: 2px;
  }
  .person {
    position: absolute;
    left: 0;
    right: 0;
    top: 248px;
    text-align: center;
  }
  .person-name {
    font-size: 64px;
  }
  .person-title {
    font-size: 21px;
    margin-top: 4px;
  }
  .contact {
    position: absolute;
    top: 448px;
    font-family: "Montserrat", Arial, sans-serif;
    font-weight: 600;
    font-size: 21px;
    font-style: normal;
    letter-spacing: 1px;
    line-height: 35px;
  }
  .contact-address { left: 62px; }
  .contact-lines { right: 65px; text-align: right; }
  .upper { text-transform: uppercase; }
</style>
</head>
<body>
  <main class="card">
    <header class="firm">
      <h1 class="serif-caps firm-name">Pacific West</h1>
      <p class="wide-sans firm-suffix">Northgate Firm, PLC</p>
    </header>

    <section class="person">
      <h2 class="serif-caps person-name">Walter Augustin Pryde</h2>
      <p class="wide-sans person-title">Attorney at Law</p>
    </section>

    <address class="contact contact-address">
      <div class="upper">2418 Cedar Lane, Suite B</div>
      <div class="upper">Alder Grove, CA 91234</div>
      <div>www.lawpwnf.com</div>
    </address>

    <address class="contact contact-lines">
      <div class="upper">Tel (555) 218-7310</div>
      <div class="upper">Fax (555) 218-7322</div>
      <div>wpryde@lawpwnf.com</div>
    </address>
  </main>
</body>
</html>
```